Need help in designing new business card utilizing our new logo.

BuildMark Solutions works with Construction Business Owners, Managers & IT Professionals to strengthen software usage and increase user productivity.

Our Construction Accounting and Mobile Field Management Software Clients engage with us in the following areas:

New Software Implementations
Software Re-Implementations
Redesigning Software Usage at the User Level
Project Coordination & Management
Continued Software Support

Old tag line:
Weighing Options - Implementing Solutions

www.buildmark-solutions.example

Ridge 4 is a product, but not needed for a new business card.

```html
<!DOCTYPE html>
<html lang="en">
<head>
<meta charset="utf-8">
<title>BuildMark Solutions – Business Card</title>
<link href="https://fonts.googleapis.com/css2?family=Open+Sans:wght@400;600;700&family=Questrial&display=swap" rel="stylesheet">
<style>
  :root {
    --backdrop: #2b2b2d;
    --card-dark: #5b5b5e;
    --card-light: #ffffff;
    --ink: #333336;
    --navy: #2b3190;
    --divider: #8a8a8c;
    --white: #ffffff;
  }
  * { box-sizing: border-box; margin: 0; padding: 0; }
  html, body {
    width: 1200px; height: 900px; overflow: hidden;
    background: var(--backdrop);
  }
  .canvas {
    position: relative; width: 1200px; height: 900px;
    display: flex; flex-direction: column; align-items: center; justify-content: center; gap: 40px;
  }
  .card {
    width: 660px; height: 377px; position: relative;
    box-shadow: 0 12px 30px rgba(0,0,0,.45);
  }
  /* Back side */
  .card--back {
    background: var(--card-dark);
    display: flex; align-items: center; justify-content: center;
  }
  .back-wordmark {
    font-family: "Open Sans", sans-serif; font-weight: 700;
    font-size: 58px; color: var(--white); letter-spacing: 1px;
  }
  /* Front side */
  .card--front {
    background: var(--card-light);
    display: flex; align-items: center;
  }
  .brand {
    width: 270px; display: flex; flex-direction: column; align-items: center; gap: 18px;
  }
  .brand-square { width: 92px; height: 92px; background: var(--navy); }
  .brand-name {
    font-family: "Open Sans", sans-serif; font-weight: 700;
    font-size: 22px; color: var(--navy);
  }
  .divider { width: 2px; height: 225px; background: var(--divider); }
  .details { padding-left: 26px; color: var(--ink); }
  .person-name {
    font-family: "Open Sans", sans-serif; font-weight: 700;
    font-size: 30px; letter-spacing: .5px; line-height: 1;
  }
  .person-role {
    font-family: "Open Sans", sans-serif; font-weight: 600;
    font-size: 17px; margin: 4px 0 10px;
  }
  .address, .contact-line {
    font-family: "Questrial", sans-serif; font-size: 17px; line-height: 1.45;
  }
  .contact-list { list-style: none; margin-top: 2px; }
  .contact-line { display: flex; align-items: center; gap: 10px; }
  .contact-icon { width: 16px; height: 16px; flex: none; }
  .web-domain { color: var(--navy); font-weight: 700; font-family: "Open Sans", sans-serif; font-size: 16px; }
</style>
</head>
<body>
<main class="canvas">
  <section class="card card--back" aria-label="Card back">
    <p class="back-wordmark">BuildMark Solutions</p>
  </section>

  <section class="card card--front" aria-label="Card front">
    <div class="brand">
      <div class="brand-square"></div>
      <p class="brand-name">BuildMark Solutions</p>
    </div>
    <div class="divider"></div>
    <div class="details">
      <h1 class="person-name">DANA R. WHITFIELD</h1>
      <p class="person-role">Owner</p>
      <p class="address">14b Harbor Lane - PMB 508<br>Millbrook Falls NY 10990</p>
      <ul class="contact-list">
        <li class="contact-line">
          <svg class="contact-icon" viewBox="0 0 16 16"><path fill="#2b3190" d="M3 1l3 3-1.5 2a9 9 0 0 0 5.5 5.5L12 10l3 3-2 2C7 15 1 9 1 3z"/></svg>
          800-555-0142 ext.100
        </li>
        <li class="contact-line">
          <svg class="contact-icon" viewBox="0 0 16 16"><rect x="4" y="1" width="8" height="14" rx="1.5" fill="none" stroke="#2b3190" stroke-width="1.8"/><circle cx="8" cy="12.3" r="1" fill="#2b3190"/></svg>
          555-014-3380
        </li>
        <li class="contact-line">
          <svg class="contact-icon" viewBox="0 0 16 16"><rect x="1" y="3" width="14" height="10" fill="#2b3190"/><path d="M1 3l7 6 7-6" fill="none" stroke="#fff" stroke-width="1.3"/></svg>
          dana.whitfield@buildmark-solutions.example
        </li>
        <li class="contact-line">
          <svg class="contact-icon" viewBox="0 0 16 16"><circle cx="9.5" cy="6.5" r="4.5" fill="none" stroke="#2b3190" stroke-width="2"/><path d="M6 10l-4.5 4.5" stroke="#2b3190" stroke-width="2.4" stroke-linecap="round"/></svg>
          <span>www.<span class="web-domain">buildmark-solutions</span>.example</span>
        </li>
      </ul>
    </div>
  </section>
</main>
</body>
</html>
```